Resposive web site in 4 languages + image gallery + logo design

We need a web page, which will work on all devices.
I have uploaded web page concept.
Company name: Praxelun
Industry/Entity Type
It Company
Logo Text
quality matters
Coding
Coded - Design and coding required
Number of Pages Required
1 page

```html
<!DOCTYPE html>
<html lang="en">
<head>
<meta charset="utf-8">
<title>Praxelun — Woodworks, Stoneworks, Restoration</title>
<link rel="stylesheet" href="https://fonts.googleapis.com/css2?family=Montserrat:wght@400;600;700&family=Open+Sans:wght@400;600&display=swap">
<style>
:root{
  --teal:#1aa394;
  --teal-dark:#12897c;
  --ink:#333333;
  --ink-soft:#555555;
  --grey-bg:#efefef;
  --card-line:#dcdcdc;
  --white:#ffffff;
  --dark:#22272b;
  --field-icon:#9a9a9a;
}
*{box-sizing:border-box;margin:0;padding:0}
html,body{width:1200px;height:2643px;overflow:hidden}
body{position:relative;background:var(--white);font-family:"Open Sans",Arial,sans-serif;color:var(--ink)}
.abs{position:absolute}

/* header */
.top-rule{left:0;top:0;width:1200px;height:5px;background:var(--teal)}
.site-header{left:0;top:5px;width:1200px;height:132px;background:var(--white)}
.brand{left:100px;top:43px;display:flex;align-items:center;gap:10px}
.brand-mark{width:16px;height:16px;background:var(--teal)}
.brand-name{font-family:"Montserrat",Arial,sans-serif;font-weight:600;font-size:30px;color:var(--teal)}
.main-nav{top:66px;left:719px;display:flex;gap:0;font-family:"Montserrat",Arial,sans-serif;font-size:12px;color:var(--ink)}
.main-nav span{position:absolute;white-space:nowrap}
.lang-switch{left:980px;top:55px;width:120px;height:36px;border:1px solid #bbb;border-radius:18px;display:flex;align-items:center;justify-content:center;gap:6px;font-family:"Montserrat",Arial,sans-serif;font-weight:600;font-size:12px}
.flag{width:16px;height:11px;background:linear-gradient(#c8102e 0 0) center/100% 3px no-repeat,linear-gradient(#c8102e 0 0) center/3px 100% no-repeat,#1f3a7a}

/* hero */
.hero{left:0;top:137px;width:1200px;height:515px;background:radial-gradient(ellipse at 50% 45%,#a88a6a 0%,#7a5d42 45%,#3f2f22 100%)}
.hero-title{left:0;top:320px;width:1200px;text-align:center;font-family:"Montserrat",Arial,sans-serif;font-weight:700;font-size:50px;color:var(--white);letter-spacing:1px}
.hero-sub{left:0;top:382px;width:1200px;text-align:center;font-family:"Open Sans",Arial,sans-serif;font-size:29px;color:var(--white)}
.hero-btn{left:522px;top:432px;width:156px;height:42px;border-radius:21px;background:var(--teal);color:var(--white);font-family:"Montserrat",Arial,sans-serif;font-weight:700;font-size:13px;display:flex;align-items:center;justify-content:center;letter-spacing:.5px}
.hero-arrow{width:42px;height:42px;top:374px;border:1.5px solid rgba(255,255,255,.55);border-radius:50%}

/* services */
.services{left:0;top:652px;width:1200px;height:1093px;background:var(--grey-bg)}
.section-title{font-family:"Montserrat",Arial,sans-serif;font-weight:700;font-size:35px;color:var(--ink);letter-spacing:.5px}
.service-card{left:99px;width:1002px;height:286px;background:var(--white);border:1px solid #e2e2e2;box-shadow:0 1px 4px rgba(0,0,0,.12)}
.service-photo{position:absolute;left:28px;top:28px;width:352px;height:229px;border:4px solid var(--white);outline:1px solid #cfcfcf}
.service-name{position:absolute;left:401px;top:30px;font-family:"Montserrat",Arial,sans-serif;font-size:19px;color:var(--ink)}
.service-text{position:absolute;left:401px;top:66px;width:572px;font-size:12.8px;line-height:28px;color:var(--ink-soft)}
.service-rule{position:absolute;left:401px;top:213px;width:572px;height:1px;background:var(--card-line)}
.service-tags{position:absolute;left:401px;top:230px;display:flex;gap:18px;font-size:12.5px;color:var(--ink)}
.service-tags span{display:flex;align-items:center;gap:6px;white-space:nowrap}
.tag-icon{width:13px;height:13px;border:2px solid var(--ink);border-radius:2px}

/* about */
.about-photo{left:127px;top:1799px;width:352px;height:226px;border:4px solid var(--white);outline:1px solid #cfcfcf;background:linear-gradient(135deg,#8a7560,#b9a58d 50%,#6d5c4b)}
.about-title{left:502px;top:1793px}
.about-text{left:500px;top:1838px;width:600px;font-size:13.4px;line-height:24px;color:var(--ink)}
.about-text p{margin-bottom:9px}

/* contact */
.contact{left:0;top:2079px;width:1200px;height:504px;background:linear-gradient(180deg,#2d3236,#1c2023 60%,#2a2622)}
.contact-title{left:0;top:2116px;width:1200px;text-align:center;color:var(--white)}
.contact-card{left:167px;top:2203px;width:346px;height:318px;background:var(--teal);padding:10px}
.contact-card-inner{width:100%;height:100%;border:1.5px solid rgba(255,255,255,.6);position:relative;color:var(--white)}
.card-brand{position:absolute;left:28px;top:32px;font-family:"Montserrat",Arial,sans-serif;font-weight:600;font-size:30px}
.card-row{position:absolute;left:28px;display:flex;gap:14px;font-size:11.5px;line-height:17px}
.card-row.phone{font-family:"Montserrat",Arial,sans-serif;font-weight:600;font-size:16px}
.form-field{left:559px;width:401px;height:40px;background:var(--white);border-radius:3px;display:flex;align-items:center;gap:12px;padding-left:14px;font-size:12.5px;color:#8a8a8a}
.form-field.message{height:102px;align-items:flex-start;padding-top:12px}
.submit-btn{left:559px;top:2497px;width:156px;height:42px;border-radius:21px;background:var(--teal);color:var(--white);font-family:"Montserrat",Arial,sans-serif;font-weight:700;font-size:13px;display:flex;align-items:center;justify-content:center;letter-spacing:.5px}

/* footer */
.site-footer{left:0;top:2583px;width:1200px;height:60px;background:var(--teal)}
.copyright{left:98px;top:2603px;font-size:12px;color:var(--white)}
.social-dot{top:2594px;width:38px;height:38px;border-radius:50%;background:#3d8fd6;box-shadow:0 2px 3px rgba(0,0,0,.25)}
</style>
</head>
<body>

<div class="abs top-rule"></div>
<header class="abs site-header"></header>
<div class="abs brand"><span class="brand-mark"></span><span class="brand-name">Praxelun</span></div>
<nav class="abs main-nav">
  <span style="left:0">SERVICES</span>
  <span style="left:91px">ABOUT US</span>
  <span style="left:187px">CONTACT</span>
</nav>
<div class="abs lang-switch"><span class="flag"></span>ENGLISH
  <svg width="8" height="6" viewBox="0 0 8 6"><path d="M1 1l3 3 3-3" fill="none" stroke="#333" stroke-width="1.5"/></svg>
</div>

<section class="abs hero" role="img" aria-label="Carpenter's hands marking a wooden board with a pencil among woodworking tools"></section>
<div class="abs hero-arrow" style="left:28px"><svg width="40" height="40" viewBox="0 0 40 40"><path d="M22 14l-6 6 6 6" fill="none" stroke="rgba(255,255,255,.7)" stroke-width="1.5"/></svg></div>
<div class="abs hero-arrow" style="left:1131px"><svg width="40" height="40" viewBox="0 0 40 40"><path d="M18 14l6 6-6 6" fill="none" stroke="rgba(255,255,255,.7)" stroke-width="1.5"/></svg></div>
<h1 class="abs hero-title">WOODWORKS</h1>
<p class="abs hero-sub">Are you interested in an estimate?</p>
<div class="abs hero-btn">GET IN TOUCH!</div>

<section class="abs services"></section>
<h2 class="abs section-title" style="left:0;top:690px;width:1200px;text-align:center">OUR SERVICES</h2>

<article class="abs service-card" style="top:768px">
  <div class="service-photo" role="img" aria-label="Craftsman planing a wooden board" style="background:linear-gradient(135deg,#5a3b25,#b88a5c 55%,#3a2618)"></div>
  <h3 class="service-name">WOODWORKS</h3>
  <p class="service-text">Timber is, in essence, a natural and warm material. Wood is also relatively durable and easy to work with, which has made it a favourite of builders throughout history. Our goal is to offer GALLERY (sliders) suitable products and quality furniture with installation and after- When cliked opens sales service to all of our clients. In order to achieve this, we're this category gallery ready to help our clients in all stages of construction from design to production and maintenance.</p>
  <div class="service-rule"></div>
  <div class="service-tags">
    <span><i class="tag-icon"></i>Furniture</span><span><i class="tag-icon"></i>Windows</span><span><i class="tag-icon"></i>Doors</span><span><i class="tag-icon"></i>Staircases</span><span><i class="tag-icon"></i>Woodcarving</span><span><i class="tag-icon"></i>Graining</span>
  </div>
</article>

<article class="abs service-card" style="top:1087px">
  <div class="service-photo" role="img" aria-label="Hands laying granite paving stones with a hammer" style="background:linear-gradient(135deg,#6e6a63,#9c958a 50%,#4a4a4c)"></div>
  <h3 class="service-name">STONEWORKS</h3>
  <p class="service-text">The natural stone found in the ground has been used in construction for centuries because of its durability. A structure built by a skilled craftsman from natural stone is unique, genuine and durable, and perfect for our bracing climate.Our experienced craftsmen are ready to help you in all stages of construction from planning to completion.The natural stone found in the ground has been used in construction for centuries because of its durability</p>
  <div class="service-rule"></div>
  <div class="service-tags" style="gap:12px">
    <span><i class="tag-icon"></i>Walls</span><span><i class="tag-icon"></i>Terraces</span><span><i class="tag-icon"></i>Paths</span><span><i class="tag-icon"></i>Outdoor kitchens</span><span><i class="tag-icon"></i>Fireplaces</span><span><i class="tag-icon"></i>Smokeries</span><span><i class="tag-icon"></i>Fences</span>
  </div>
</article>

<article class="abs service-card" style="top:1403px">
  <div class="service-photo" role="img" aria-label="Hand sanding an old wooden chair seat" style="background:linear-gradient(135deg,#1e120c,#8a4f2a 55%,#2a160c)"></div>
  <h3 class="service-name">RESTORATION</h3>
  <p class="service-text">It's good to see that fixing old things has become popular again in recent years and people are trying to find ways to preserve valuable old windows and pieces of furniture before deciding to replace them. It is possible to give a new life to almost any wooden door, window, piece of furniture or staircase. The extensive experience of our craftsmen will help you achieve the desired result. It's good to see that fixing old things has become popular again in recent years</p>
  <div class="service-rule"></div>
  <div class="service-tags">
    <span><i class="tag-icon"></i>Furniture</span><span><i class="tag-icon"></i>Windows</span><span><i class="tag-icon"></i>Doors</span><span><i class="tag-icon"></i>Staircases</span><span><i class="tag-icon"></i>Floors</span><span><i class="tag-icon"></i>Special Projects</span>
  </div>
</article>

<div class="abs about-photo" role="img" aria-label="Two craftsmen working in a woodworking shop"></div>
<h2 class="abs section-title about-title">ABOUT US</h2>
<div class="abs about-text">
  <p>Praxelun is a company whose business operations include making wooden products, restoration and building structures from natural stone.</p>
  <p>All of our products are made by craftsmen and specialists who have extensive experience and knowledge in their fields.</p>
  <p>The products we offer are always handmade and we take the requests and ideas of the specific client into account We always strive to achieve the best possible quality.</p>
  <p>Quality matters, Praxelun</p>
</div>

<section class="abs contact" role="img" aria-label="Dim workshop background with woodworking hands and tools"></section>
<h2 class="abs section-title contact-title">CONTACT US</h2>

<div class="abs contact-card">
  <div class="contact-card-inner">
    <div class="card-brand">Praxelun</div>
    <div class="card-row" style="top:96px">
      <svg width="12" height="16" viewBox="0 0 12 16"><path d="M6 0a6 6 0 0 0-6 6c0 4.5 6 10 6 10s6-5.5 6-10a6 6 0 0 0-6-6zm0 8.5A2.5 2.5 0 1 1 6 3.5a2.5 2.5 0 0 1 0 5z" fill="#fff"/></svg>
      <div>Lepa 7<br>10411 Tartu<br>ESTONIA</div>
    </div>
    <div class="card-row phone" style="top:172px">
      <svg width="15" height="15" viewBox="0 0 16 16"><path d="M3.5 1l2.5 3-1.5 1.8a9 9 0 0 0 5.7 5.7L12 10l3 2.5-1.5 2.5C7 15 1 9 1 2.5z" fill="#fff"/></svg>
      <div>+372 55 01 2380</div>
    </div>
    <div class="card-row" style="top:216px">
      <svg width="16" height="12" viewBox="0 0 16 12"><rect x=".5" y=".5" width="15" height="11" fill="#fff"/><path d="M1 1l7 5.5L15 1" fill="none" stroke="#1aa394" stroke-width="1.3"/></svg>
      <div>hello@praxelun.ee</div>
    </div>
  </div>
</div>

<div class="abs form-field" style="top:2206px"><svg width="14" height="14" viewBox="0 0 14 14"><circle cx="7" cy="4" r="3.5" fill="#9a9a9a"/><path d="M0 14a7 6 0 0 1 14 0z" fill="#9a9a9a"/></svg>Your name</div>
<div class="abs form-field" style="top:2264px"><svg width="14" height="14" viewBox="0 0 16 16"><path d="M3.5 1l2.5 3-1.5 1.8a9 9 0 0 0 5.7 5.7L12 10l3 2.5-1.5 2.5C7 15 1 9 1 2.5z" fill="#9a9a9a"/></svg>Phone number</div>
<div class="abs form-field" style="top:2320px"><svg width="16" height="12" viewBox="0 0 16 12"><rect width="16" height="12" fill="#9a9a9a"/><path d="M1 1l7 5.5L15 1" fill="none" stroke="#fff" stroke-width="1.3"/></svg>Email address</div>
<div class="abs form-field message" style="top:2379px"><svg width="14" height="14" viewBox="0 0 14 14"><path d="M1 13l1-4 8-8 3 3-8 8z" fill="#9a9a9a"/></svg>Message</div>
<div class="abs submit-btn">SUBMIT</div>

<footer class="abs site-footer"></footer>
<p class="abs copyright">Copyright 2016 Praxelun. All Rights Reserved</p>
<div class="abs social-dot" style="left:969px"></div>
<div class="abs social-dot" style="left:1013px;background:#3ba7e0"></div>
<div class="abs social-dot" style="left:1058px;background:#3f7fc4"></div>

</body>
</html>
```